The Velvet Easel Co - Photos to Custom Oil Paintings

We need a website and logo designed and built allowing customers to purchase custom oil paintings. The paintings will come from a customers single photograph or even combination of photos. They will be able to complete a straight forward checkout process, selecting their desired medium (oil or charcoal painting), their desired size, the number of figures in the painting, the type of background required (as per photo or let the artist decide). Which will then automaticaly provide the customer with a price for the purchase. Allowing them to add a photo to the order which they can then submit with the order present in their personal account etc etc etc.
Theres one website in particular that i will be competing with. That is based in the US - http://www.brushmorrow.com
I wish to far exceed the appearence of the already present site.
At the moment i wish to include Coinvale in the payment process. Unless there are some cheaper, more cost efficient ways, please let me know.
The company name is The Velvet Easel Co. Domain has been purchased - www.thevelveteasel.co (via Hostlark - Linux)
I have no great sense of design, but the site must be straight forward, eye catching, engaging and give the customer a sense of high quality. Some kind of flash animation with pictures on the front page scrolling?
For myself, the admin side, ideally must be straight forward to maintain. The ability to update customers accounts with info (they will then be informed there is an update in their account etc)
The ability for automated emails from point of sale (sales orders with generated order numbers) to myself. Again automated emails to the customers once the "status" of their order or other information has been submitted to their account (by myself) or a similar system.
Updates
All,
Please note, the budget is able to increase subject to what additional work is needed. As far as the admin area goes. I am open to suggestions to ensure ease of use and efficiency.
Any questions, comments or ideas are fully welcomed.
Many thanks,
Dan Holloway
Industry/Entity Type
It Company
Logo Text
Logo styles of interest
Pictorial/Combination Logo
Abstract Logo
Wordmark Logo
Lettermark Logo
Look and feel
Each slider illustrates characteristics of the customer's brand and the style your logo design should communicate.

```html
<!DOCTYPE html>
<html lang="en">
<head>
<meta charset="utf-8">
<title>The Velvet Easel Co</title>
<link rel="stylesheet" href="https://fonts.googleapis.com/css2?family=Source+Sans+3:ital,wght@0,400;0,600;1,400&family=Dancing+Script:wght@600&display=swap">
<style>
:root{
  --teal:#14958f;
  --teal-light:#3bb3ad;
  --teal-text:#128580;
  --page-bg:#f8f4e7;
  --panel:#ece8dc;
  --ink:#333;
  --muted:#6b6b6b;
  --footer:#3a3a3a;
  --white:#fff;
}
*{margin:0;padding:0;box-sizing:border-box}
html,body{width:1091px;height:1200px;overflow:hidden;background:var(--page-bg)}
body{font-family:"Source Sans 3",sans-serif;color:var(--ink)}
.stage{width:1000px;height:1100px;position:relative;transform:scale(1.091);transform-origin:0 0}
.abs{position:absolute}
.header{left:0;top:0;width:1000px;height:445px;background:repeating-linear-gradient(135deg,#ebe6da 0 2px,#e4dfd2 2px 4px);border-bottom:1px solid #d8d2c2}
.social{right:24px;top:12px;display:flex;gap:10px;align-items:center}
.social span{display:flex;align-items:center;gap:3px;font-size:10px;color:var(--muted)}
.social i{width:10px;height:10px;border-radius:50%;background:var(--white);border:1px solid #cfc9ba}
.ribbon{left:18px;top:46px;width:962px;height:54px}
.palette{left:18px;top:36px;width:76px;height:72px;border-radius:50%;background:radial-gradient(circle at 35% 35%,#f6e2cf 0,#e8c3a3 45%,#c99a78 100%);box-shadow:0 2px 4px rgba(0,0,0,.25)}
.logo-name{left:100px;top:56px;font-size:30px;font-weight:600;color:var(--white);letter-spacing:.5px}
.nav{left:389px;top:46px;height:54px;display:flex}
.nav a{display:block;height:54px;line-height:54px;padding:0 26px;color:var(--white);font-size:15px;text-decoration:none}
.nav a.current{background:var(--teal-light);padding:0 21px}
.categories{left:52px;top:146px;display:grid;grid-template-columns:168px 150px;row-gap:10px}
.categories li{list-style:none;font-size:15px;color:#7a7a7a;padding-left:22px;position:relative;height:22px}
.categories li::before{content:"";position:absolute;left:2px;top:7px;width:6px;height:6px;border-right:2px solid #777;border-top:2px solid #777;transform:rotate(45deg)}
.categories li.active{color:#2b2b2b}
.categories li.active::before{border-color:#2b2b2b}
.upload{left:40px;top:305px;width:311px;height:67px;border-radius:6px;background:#d7d2c5;border:1px solid #cbc5b6}
.upload-icon{left:34px;top:302px;width:84px;height:84px;border-radius:6px;background:radial-gradient(circle at 50% 45%,#9cc3ec 0,#5d8fcf 30%,#e6e6e6 42%,#bcbcbc 100%);box-shadow:0 2px 4px rgba(0,0,0,.3)}
.upload-text{left:134px;top:316px;color:#555}
.upload-text small{display:block;font-size:14px}
.upload-text strong{display:block;font-size:23px;font-weight:400;color:#444;line-height:1.1}
.slider{left:391px;top:116px;width:586px;height:270px;background:var(--white);padding:6px;box-shadow:0 1px 4px rgba(0,0,0,.25)}
.slide{width:100%;height:100%;background:radial-gradient(ellipse at 45% 40%,#b09676 0,#a2876a 55%,#8f755a 100%);position:relative;overflow:hidden}
.slide::after{content:"";position:absolute;left:-40px;bottom:-60px;width:260px;height:160px;border-radius:50%;background:radial-gradient(ellipse,rgba(220,200,175,.35),rgba(220,200,175,0) 70%)}
.slide-title{position:absolute;left:37px;top:38px;font-family:"Dancing Script",cursive;font-size:24px;color:var(--white)}
.slide-photo-small{position:absolute;left:264px;top:88px;width:90px;height:124px;background:linear-gradient(180deg,#6d7e90 0,#b89b86 45%,#8a6a58 70%,#5f5a5a 100%);border:5px solid var(--white);box-shadow:4px 6px 10px rgba(0,0,0,.4);transform:rotate(3deg)}
.slide-photo-large{position:absolute;left:408px;top:16px;width:152px;height:228px;background:linear-gradient(180deg,#2f3b48 0,#566273 20%,#b98d70 45%,#8b5a44 65%,#5a4438 100%);border:2px solid var(--white);box-shadow:3px 5px 10px rgba(0,0,0,.4)}
.dots{left:440px;top:403px;width:520px;height:16px}
.section-label{left:48px;top:463px;font-size:15px;color:#333}
.gallery{left:39px;top:493px;width:925px;height:151px;background:var(--panel);border-radius:6px}
.thumb{top:514px;width:192px;height:111px;box-shadow:0 1px 3px rgba(0,0,0,.3)}
.arrow{top:552px;width:28px;height:38px}
h2{font-weight:400;font-size:21px;color:var(--teal-text)}
.welcome-h{left:16px;top:666px}
.copy{font-size:13px;line-height:20px;text-align:justify;color:var(--ink)}
.welcome-p{left:17px;top:704px;width:622px}
.gift-h{left:16px;top:850px}
.gift-img{left:25px;top:894px;width:222px;height:110px;background:radial-gradient(ellipse at 40% 45%,#b07a52 0,#6b4a32 30%,#2e211a 75%,#1c1410 100%);border:2px solid var(--white);box-shadow:0 1px 3px rgba(0,0,0,.35)}
.gift-p{left:267px;top:888px;width:374px}
.testi-h{left:687px;top:666px}
.view-all{left:922px;top:674px;font-size:11px;color:#333}
.testimonials{left:688px;top:708px;width:278px;height:312px;background:var(--panel);border:1px solid #ddd8ca;box-shadow:0 1px 4px rgba(0,0,0,.25)}
.person{position:absolute;left:16px;width:82px;height:78px}
.quote{position:absolute;left:108px;font-size:12px;line-height:20px;width:160px}
.quote b{font-weight:400;color:#222;display:block}
.quote em{color:#777}
.footer{left:0;top:1035px;width:1000px;height:65px;background:var(--footer);border-top:2px solid #cfcabd}
.copyright{left:19px;top:1062px;font-size:13px;color:var(--white)}
.payments{right:36px;top:1062px;display:flex;gap:6px}
.payments span{font-size:10px;color:#333;background:#f2f2f2;border-radius:2px;padding:2px 4px;line-height:14px}
</style>
</head>
<body>
<div class="stage">
  <div class="abs header"></div>

  <div class="abs social">
    <span><i></i>Friendnest</span>
    <span><i></i>Chirpline</span>
    <span><i></i>Searchly</span>
    <span><i></i>Yodelo</span>
    <span><i></i>Postwell</span>
  </div>

  <svg class="abs ribbon" viewBox="0 0 962 54" aria-hidden="true">
    <defs>
      <linearGradient id="band" x1="0" y1="0" x2="0" y2="1">
        <stop offset="0" stop-color="#1fa9a2"/>
        <stop offset="1" stop-color="#0e7f7a"/>
      </linearGradient>
    </defs>
    <path d="M30 0H962L936 27L962 54H30Z" fill="url(#band)"/>
    <rect x="30" y="52" width="906" height="2" fill="#0a6560"/>
  </svg>
  <div class="abs palette" role="img" aria-label="Artist paint palette with colour daubs"></div>
  <div class="abs logo-name">The Velvet Easel</div>
  <nav class="abs nav">
    <a class="current" href="#">Home</a>
    <a href="#">About Us</a>
    <a href="#">Our Gallery</a>
    <a href="#">Testimonials</a>
    <a href="#">Contact Us</a>
  </nav>

  <ul class="abs categories">
    <li>Wedding Photos</li><li>Family Photos</li>
    <li class="active">Child Photos</li><li>Self Photos</li>
    <li>Pet Photos</li><li>Wedding Photos</li>
    <li>Friends Photos</li><li>Child Photos</li>
  </ul>

  <div class="abs upload"></div>
  <div class="abs upload-icon" role="img" aria-label="Picture frame icon with a portrait silhouette"></div>
  <div class="abs upload-text"><small>Click Here for</small><strong>Upload your Photo</strong></div>

  <div class="abs slider">
    <div class="slide">
      <div class="slide-title">Excepteur sint occaecat cupidata</div>
      <div class="slide-photo-small" role="img" aria-label="Small printed photo of a child held in a hand"></div>
      <div class="slide-photo-large" role="img" aria-label="Painted portrait of a young child resting chin on hand"></div>
    </div>
  </div>
  <svg class="abs dots" viewBox="0 0 520 16" aria-hidden="true">
    <line x1="0" y1="8" x2="210" y2="8" stroke="#b9b3a4"/>
    <line x1="300" y1="8" x2="520" y2="8" stroke="#b9b3a4"/>
    <circle cx="230" cy="8" r="4" fill="#8d8d8d"/>
    <circle cx="248" cy="8" r="6" fill="#fff" stroke="#2aa7a0" stroke-width="2"/>
    <circle cx="248" cy="8" r="3" fill="#2aa7a0"/>
    <circle cx="266" cy="8" r="4" fill="#8d8d8d"/>
    <circle cx="284" cy="8" r="4" fill="#8d8d8d"/>
  </svg>

  <div class="abs section-label">Our Gallery</div>
  <div class="abs gallery"></div>
  <svg class="abs arrow" style="left:50px" viewBox="0 0 28 38" aria-hidden="true"><path d="M22 4L8 19L22 34" fill="none" stroke="#8a8a8a" stroke-width="6"/></svg>
  <svg class="abs arrow" style="left:918px" viewBox="0 0 28 38" aria-hidden="true"><path d="M6 4L20 19L6 34" fill="none" stroke="#8a8a8a" stroke-width="6"/></svg>
  <div class="abs thumb" style="left:100px;background:radial-gradient(ellipse at 50% 45%,#d6d6d6 0,#8e8e8e 35%,#4a4a4a 75%,#2e2e2e 100%)" role="img" aria-label="Black and white portrait of an older man"></div>
  <div class="abs thumb" style="left:303px;background:radial-gradient(ellipse at 50% 60%,#f0d8c4 0,#d9b48a 30%,#b08a5c 65%,#e8e2da 100%)" role="img" aria-label="Portrait of a young woman in a straw hat"></div>
  <div class="abs thumb" style="left:506px;background:radial-gradient(ellipse at 50% 55%,#f0c8a8 0,#c7cde6 35%,#7c5a8c 75%,#5a3e6a 100%)" role="img" aria-label="Painting of a baby in a blue outfit"></div>
  <div class="abs thumb" style="left:708px;background:linear-gradient(90deg,#6b4a3a 0,#c48a70 35%,#b87a66 55%,#e8e4e0 75%,#cfc8c0 100%)" role="img" aria-label="Wedding couple kissing"></div>

  <h2 class="abs welcome-h">Welcome to our site</h2>
  <p class="abs copy welcome-p">Sed ut perspiciatis unde omnis iste natus error sit voluptatem accusantium doloremque laudantium, totam rem aperiam, eaque ipsa quae ab illo inventore veritatis et quasi architecto beatae vitae dicta sunt explicabo. Nemo enim ipsam voluptatem quia voluptas sit aspernatur aut odit aut fugit, sed quia consequuntur magni dolores eos qui ratione voluptatem sequi nesciunt. Neque porro quisquam est, qui dolorem ipsum quia dolor sit amet, consectetur, adipisci velit, sed quia non numquam eius modi tempora incidunt ut labore et dolore magnam aliquam quaerat voluptatem. Ut enim ad minima veniam.</p>

  <h2 class="abs gift-h">Gift Ideas</h2>
  <div class="abs gift-img" role="img" aria-label="Classical oil portrait painting"></div>
  <p class="abs copy gift-p">Sed ut perspiciatis unde omnis iste natus error sit voluptatem accusantium doloremque laudantium, totam rem aperiam, eaque ipsa quae ab illo inventore veritatis et quasi architecto beatae vitae dicta sunt explicabo. Nemo enim ipsam voluptatem quia voluptas sit aspernatur aut odit aut fugit, sed quia consequuntur magni dolores eos qui ratione voluptatem sequi nesciunt.</p>

  <h2 class="abs testi-h">Testimonials</h2>
  <div class="abs view-all">View all</div>
  <div class="abs testimonials">
    <div class="person" style="top:20px;background:radial-gradient(ellipse at 50% 60%,#d8a890 0,#9a6a58 35%,#3e3e3e 80%)" role="img" aria-label="Customer photo, man in a cap"></div>
    <div class="quote" style="top:28px"><b>Nemo enim ipsam</b><em>voluptatem quia voluptas sit aspernatur autodit autfugit</em></div>
    <div class="person" style="top:117px;background:#3a3a3a;padding:6px"><div style="width:100%;height:100%;background:#c8c8c8" role="img" aria-label="Placeholder avatar"></div></div>
    <div class="quote" style="top:125px"><b>Nemo enim ipsam</b><em>voluptatem quia voluptas sit aspernatur autodit autfugit</em></div>
    <div class="person" style="top:212px;background:radial-gradient(ellipse at 50% 45%,#f0d4bc 0,#c89a70 35%,#a8784e 60%,#e4ddd4 100%)" role="img" aria-label="Customer photo, woman with glasses"></div>
    <div class="quote" style="top:220px"><b>Nemo enim ipsam</b><em>voluptatem quia voluptas sit aspernatur autodit autfugit</em></div>
  </div>

  <div class="abs footer"></div>
  <div class="abs copyright">Copyright © 2012 www.thevelveteasel.co &nbsp; All rights reserved</div>
  <div class="abs payments">
    <span>Coinvale</span><span>Cardwell</span><span>Payrise</span><span>Tillpoint</span><span>Veyra</span>
  </div>
</div>
</body>
</html>
```